uk based ecommerce website requires fresh look ,high quality look and feel

we are a web based company selling eco friendly ground reinforcement grids to diy and construction sectors
our existing website is www.pondermeshpaths.co.uk ,

we have already updated the logo so that is the branding sorted .so we need a ecommerce website that is very much up-to date in design and layout and which has content management system for ease of use so that we can add products and information as required.

Use current logo as reference for colour scheme.
www.pondermeshpaths.co.uk

The current website has 6 pages accessible through the navigation bar, I would now like 5 pages, removing the need for the Trade Enquiries page possibly have it with along with contact us.

Target Market(s)

construction industry , diy end users,
retail market, landscapers, gardeners

Industry/Entity Type

Construction

Font styles to use
Other font styles liked:
• logo font prometo

Colors
f78f20
9bcb3c

Requirements
Must have
• logo colours and logo design in website with cms responsive design for tablet and mobile devices
• expect content to work flawlessly and look great across all devices
• HTML 5 custom design with coding as required
• must have good experiance in ecommerce website design
• eye catching, high quality look and feel and very user friedly ,very up-to date.
Nice to have
• picture slider show
• explain in writing what exactly i am getting in my ecommerce website
Should not have
• plain , basic design , old fashion looking ,cheap look

```html
<!DOCTYPE html>
<html lang="en">
<head>
<meta charset="utf-8">
<title>Pondermesh Ground Solutions</title>
<link href="https://fonts.googleapis.com/css2?family=Exo+2:wght@500;600;700&family=Open+Sans:wght@400;600;700&display=swap" rel="stylesheet">
<style>
:root{
  --orange:#f78f20;
  --orange-dark:#e57c0e;
  --green:#9bcb3c;
  --green-dark:#6fa52a;
  --grass:#5fa82c;
  --text:#666;
  --text-dark:#333;
  --footer:#2f2f2f;
  --white:#fff;
}
*{margin:0;padding:0;box-sizing:border-box}
html,body{width:706px;height:1200px;overflow:hidden}
body{position:relative;font-family:"Open Sans",sans-serif;color:var(--text);
  background:var(--grass) repeating-linear-gradient(45deg,rgba(255,255,255,.05) 0 3px,transparent 3px 6px);}
.abs{position:absolute}
.topbar{left:0;top:0;width:706px;height:14px;background:var(--orange)}
.page{left:39px;top:14px;width:627px;height:1023px;background:var(--white)}
.toplinks{right:60px;top:3px;display:flex;gap:13px;font-size:5.5px;color:#fff;text-transform:uppercase}
.logo{left:58px;top:20px;display:flex;align-items:center;gap:6px}
.logo .mark{width:28px;height:44px;border-radius:4px;background:var(--green)}
.logo .name{font-family:"Exo 2",sans-serif;font-weight:700;font-size:11px;color:var(--orange);line-height:1.1}
.logo .name small{display:block;font-size:6.5px;color:var(--text-dark)}
.search{left:417px;top:37px;width:101px;height:14px;border:1px solid #ddd;font-size:5px;color:#999;display:flex;align-items:center;padding-left:5px}
.search span{margin-left:auto;background:var(--green);color:#fff;height:100%;padding:0 6px;display:flex;align-items:center}
.cart{left:563px;top:37px;width:84px;height:14px;border:1px solid #ddd;font-size:5px;display:flex;align-items:center;justify-content:center;color:var(--text-dark)}
.cart b{color:var(--orange);font-weight:400;margin-left:2px}
.nav{left:176px;top:73px;width:471px;height:28px;background:var(--orange);display:flex;font-size:7.5px;color:#fff;text-transform:uppercase}
.nav div{padding:0 18px;display:flex;align-items:center;border-right:1px solid var(--orange-dark)}
.nav div:first-child{padding-left:20px}
.products{left:52px;top:73px;width:132px;height:28px;background:linear-gradient(var(--green),var(--green-dark));
  clip-path:polygon(10px 0,122px 0,132px 50%,122px 100%,10px 100%,0 50%);color:#fff;font-family:"Exo 2",sans-serif;font-weight:700;font-size:9px;display:flex;align-items:center;justify-content:center}
.sidebar{left:58px;top:110px;width:120px;height:247px;background:var(--orange)}
.sidebar div{height:24.7px;border-bottom:1px solid var(--orange-dark);font-size:5.8px;color:#fff;display:flex;align-items:center;padding-left:9px;text-transform:uppercase}
.sidebar .active{background:var(--green)}
.slider{left:190px;top:110px;width:457px;height:247px;background:linear-gradient(120deg,#4f8f2a,#8fa07a 45%,#6b5346 80%)}
.slide-text{left:210px;top:192px;color:#fff}
.slide-text h2{font-family:"Exo 2",sans-serif;font-weight:700;font-size:19px}
.slide-text h3{font-size:7px;font-weight:700;margin-top:2px}
.slide-text p{font-size:6.5px;width:180px;line-height:1.8;margin-top:3px}
.slide-btn{left:211px;top:264px;width:82px;height:24px;background:var(--green);color:#fff;font-size:7px;font-weight:700;display:flex;align-items:center;justify-content:center}
.arrows{left:599px;top:309px;display:flex;gap:2px}
.arrows span{width:13px;height:13px;background:var(--orange);color:#fff;font-size:8px;display:flex;align-items:center;justify-content:center}
h2.section{font-family:"Exo 2",sans-serif;font-weight:700;color:var(--orange);font-size:12.5px;letter-spacing:.3px}
.intro{left:58px;top:382px;width:322px;font-size:6.5px;line-height:16px}
.intro p{margin-top:4px}
.intro h4{color:var(--orange);font-size:8px;margin:6px 0 2px}
.intro .note{color:var(--text-dark);font-size:7px;line-height:14px;margin-top:10px}
.gallery-line{left:418px;top:387px;width:229px;height:1px;background:#e5e5e5}
.gallery-dots{left:525px;top:383px;display:flex;gap:3px}
.gallery-dots span{width:8px;height:8px;border-radius:50%;background:#bbb}
.gallery{left:420px;top:402px}
.adv-title{left:0;width:706px;top:741px;text-align:center}
.adv{top:778px;width:290px;font-size:7.5px;line-height:16px;color:#777}
.adv li{list-style:none;position:relative;padding-left:17px;margin-bottom:13px}
.adv li svg{position:absolute;left:0;top:4px}
.footer{left:39px;top:1037px;width:627px;height:133px;background:var(--footer);color:#ccc;font-size:6px}
.fcol{top:14px}
.fcol h5{color:var(--green);font-size:7.5px;font-weight:600;padding-bottom:6px;border-bottom:1px solid #555;margin-bottom:6px}
.fcol ul li{margin-left:8px;line-height:13px}
.fcol ul li.on{color:var(--green)}
.contact-row{display:flex;gap:6px;margin-bottom:6px;line-height:10px}
.social{display:grid;grid-template-columns:68px 68px;row-gap:10px;font-size:7px;color:#ddd}
.social div{display:flex;align-items:center;gap:6px}
.social i{width:17px;height:17px;border-radius:50%;border:2px solid}
.cards{display:flex;gap:3px;margin-top:10px}
.cards span{width:22px;height:13px;border-radius:2px;background:#eee}
.bottom{left:0;top:1170px;width:706px;height:30px;background:var(--orange)}
.bottom p{text-align:center;color:#fff;font-size:6.5px;line-height:30px}
</style>
</head>
<body>
<div class="abs topbar"></div>
<div class="abs page"></div>
<div class="abs toplinks"><span>Home</span><span>|</span><span>My Account</span><span>|</span><span>Login</span><span>|</span><span>Register</span></div>

<div class="abs logo"><div class="mark"></div><div class="name">PONDERMESH<small>GROUND SOLUTIONS</small></div></div>
<div class="abs search">SEARCH YOUR ITEMS :<span>SEARCH</span></div>
<div class="abs cart">YOUR CART IS : <b>0 ITEMS</b></div>

<div class="abs nav"><div>Shop</div><div>About us</div><div>Ground Solutions</div><div>Pondermesh</div><div style="border:0">Contact us</div></div>
<div class="abs products">PRODUCTS &nbsp;&#8964;</div>

<div class="abs sidebar">
  <div>Geotextile membranes</div><div class="active">Light domestic driveways</div><div>Heavy domestic driveways</div>
  <div>Parking and pathway system</div><div>Grass reinforcement mesh &amp;</div><div>Turf reinforcement mesh</div>
  <div>Steel U pins</div><div>Commercial parking system</div><div>Equiform grid</div><div style="border:0">Monthly specials</div>
</div>

<div class="abs slider" role="img" aria-label="Aerial view of a curved gravel path through lawn beside a timber deck"></div>
<div class="abs slide-text"><h2>PONDERMESH ECO</h2><h3>SOLUTIONS LTD STABILISED GRAVEL</h3><p>Part of a natural porous paving system, when filled with gravel this gives you an eco-friendly</p></div>
<div class="abs slide-btn">VIEW PRODUCT</div>
<div class="abs arrows"><span>&#8249;</span><span>&#8250;</span></div>

<div class="abs intro">
  <h2 class="section">GROUND REINFORCEMENT GRIDS FOR GRAVEL</h2>
  <p>PONDERMESH gravel systems use of retaining grids that holds together gravel for all paving uses including vehicle and pedestrian used areas.</p>
  <p>Part of a natural porous paving system, when filled with gravel this gives you an eco-friendly surface that costs less than other forms of paving</p>
  <p>THE PONDERMESH system solves the old problems related to gravel driveways as this won't sink, migrate or form ruts but will perform well and produce a hold</p>
  <p>The underside of the grids have a durable geotextile membrane layer infused to the underside of the grid which has an extra purpose as a water filtration layer which also allows water drainage and also stops any weed growth and gravel reduction. All grids are easy to install and are even suited to sloped areas too.</p>
  <h4>INFORMATION NOTE:</h4>
  <p class="note">Gravel size 10mm to 14mm optimal size</p>
  <p class="note">type of stone angular cut or flint type</p>
  <p class="note">warning pea gravel is not ideal due to loss of traction on hills and entrance ways and exits so not suitable for vehicular traffic .</p>
</div>

<div class="abs gallery-line"></div>
<div class="abs gallery-dots"><span></span><span></span></div>
<svg class="abs gallery" width="230" height="320" viewBox="0 0 230 320" role="img" aria-label="Hexagon gallery of gravel grids, installed driveways and paths">
  <defs><polygon id="hx" points="33,0 66,18 66,54 33,72 0,54 0,18"/><polygon id="hi" points="33,4 62,20 62,52 33,68 4,52 4,20"/></defs>
  <g stroke="#f78f20" stroke-width="2" fill="#fff">
    <use href="#hx" x="3" y="2"/><use href="#hx" x="82" y="2"/><use href="#hx" x="161" y="2"/>
    <use href="#hx" x="3" y="82"/><use href="#hx" x="82" y="82"/><use href="#hx" x="161" y="82"/>
    <use href="#hx" x="3" y="162"/><use href="#hx" x="82" y="162"/><use href="#hx" x="161" y="162"/>
    <use href="#hx" x="3" y="242"/><use href="#hx" x="82" y="242"/><use href="#hx" x="161" y="242"/>
  </g>
  <use href="#hi" x="3" y="2" fill="#4a4a3e"/><use href="#hi" x="82" y="2" fill="#8a5a6a"/><use href="#hi" x="161" y="2" fill="#4f7a3a"/>
  <use href="#hi" x="3" y="82" fill="#3c3c3c"/><use href="#hi" x="82" y="82" fill="#7a7a72"/><use href="#hi" x="161" y="82" fill="#9aa08a"/>
  <use href="#hi" x="3" y="162" fill="#6a7490"/><use href="#hi" x="82" y="162" fill="#5a4a3a"/><use href="#hi" x="161" y="162" fill="#555"/>
  <use href="#hi" x="3" y="242" fill="#3a352e"/><use href="#hi" x="82" y="242" fill="#b0aa9a"/><use href="#hi" x="161" y="242" fill="#4a4a48"/>
</svg>

<div class="abs adv-title"><h2 class="section">ADVANTAGES OF PONDERMESH STRUCTURES</h2></div>
<ul class="abs adv" style="left:74px">
  <li><svg width="8" height="7" viewBox="0 0 8 7"><path d="M1 3.5l2 2 4-4.5" stroke="#9bcb3c" stroke-width="1.6" fill="none"/></svg>Stabilise gravel. Get the gravel to stay put, no holes, no sinking, no problems.</li>
  <li><svg width="8" height="7" viewBox="0 0 8 7"><path d="M1 3.5l2 2 4-4.5" stroke="#9bcb3c" stroke-width="1.6" fill="none"/></svg>Low cost the gravel won't move around you can use less, giving you a porous paving that costs less than concrete,tarmacadams or block Pavers.</li>
  <li><svg width="8" height="7" viewBox="0 0 8 7"><path d="M1 3.5l2 2 4-4.5" stroke="#9bcb3c" stroke-width="1.6" fill="none"/></svg>Super strong. Enhanced load bearing causes no rutting, separating or sliding with vehicle traffic. Gravel or grass infill.</li>
  <li><svg width="8" height="7" viewBox="0 0 8 7"><path d="M1 3.5l2 2 4-4.5" stroke="#9bcb3c" stroke-width="1.6" fill="none"/></svg>No weeds or gravel loss, The geotextile membrane underneath the grids prevents this.</li>
  <li><svg width="8" height="7" viewBox="0 0 8 7"><path d="M1 3.5l2 2 4-4.5" stroke="#9bcb3c" stroke-width="1.6" fill="none"/></svg>Environmentally friendly which is SUDS compliant, With all our systems being porous it is ideal for solutions requiring a Sustainable</li>
</ul>
<ul class="abs adv" style="left:366px">
  <li><svg width="8" height="7" viewBox="0 0 8 7"><path d="M1 3.5l2 2 4-4.5" stroke="#9bcb3c" stroke-width="1.6" fill="none"/></svg>Stabilise gravel. Get the gravel to stay put, no holes, no sinking, no problems.</li>
  <li><svg width="8" height="7" viewBox="0 0 8 7"><path d="M1 3.5l2 2 4-4.5" stroke="#9bcb3c" stroke-width="1.6" fill="none"/></svg>Low cost the gravel won't move around you can use less, giving you a porous paving that costs less than concrete,tarmacadams or block Pavers.</li>
  <li><svg width="8" height="7" viewBox="0 0 8 7"><path d="M1 3.5l2 2 4-4.5" stroke="#9bcb3c" stroke-width="1.6" fill="none"/></svg>Super strong. Enhanced load bearing causes no rutting, separating or sliding with vehicle traffic. Gravel or grass infill.</li>
  <li><svg width="8" height="7" viewBox="0 0 8 7"><path d="M1 3.5l2 2 4-4.5" stroke="#9bcb3c" stroke-width="1.6" fill="none"/></svg>No weeds or gravel loss, The geotextile membrane underneath the grids prevents this.</li>
  <li><svg width="8" height="7" viewBox="0 0 8 7"><path d="M1 3.5l2 2 4-4.5" stroke="#9bcb3c" stroke-width="1.6" fill="none"/></svg>Environmentally friendly which is SUDS compliant, With all our systems being porous it is ideal for solutions requiring a Sustainable</li>
</ul>

<div class="abs footer">
  <div class="abs fcol" style="left:35px;width:83px"><h5>QUICK LINKS</h5>
    <ul><li>Shop</li><li class="on">About us</li><li>Ground Solutions</li><li>Pondermesh</li><li>Customer Services</li><li>Request a Quote</li><li>Contact Us</li></ul></div>
  <div class="abs fcol" style="left:137px;width:140px"><h5>CONTACT INFO</h5>
    <div class="contact-row"><svg width="7" height="7" viewBox="0 0 10 10"><path d="M2 1l2 2-1 1.5c.8 1.5 1.5 2.2 3 3L7.5 6l2 2-1.5 1.5C4.5 9 1 5.5.5 2.5z" fill="#f78f20"/></svg><div><b style="color:#fff;font-size:7px;font-weight:600">0149-555-0142 | 0845-555-0178</b><br>24 Hour Messaging Service</div></div>
    <div class="contact-row"><svg width="7" height="8" viewBox="0 0 10 12"><path d="M5 0a4 4 0 014 4c0 3-4 8-4 8S1 7 1 4a4 4 0 014-4z" fill="#f78f20"/></svg><div>Brackenfold House, Larchside Ind Est,<br>Dunmere DN4 7QX</div></div>
    <div class="contact-row"><svg width="7" height="7" viewBox="0 0 10 10"><path d="M0 5L10 0 7 10 5 6z" fill="#f78f20"/></svg><div>sales@pondermeshpaths.co.uk<br>Mon to Fri-9.00am to 6.00pm</div></div></div>
  <div class="abs fcol" style="left:302px;width:135px"><h5>TESTIMONIALS</h5>
    <div style="text-align:center;font-size:12px;color:#aaa;line-height:10px">&ldquo;</div>
    <p style="line-height:11px;margin-top:3px">Quality products at an affordable price and which meets the requirements of our customers. We supply a permeable paving system that keeps the traditional</p>
    <p style="margin-top:6px;line-height:11px"><b style="color:#fff;font-weight:600">Maren Tolvey</b>,Manager<br>Fernway Landscapes</p></div>
  <div class="abs fcol" style="left:469px;width:139px"><h5>FOLLOW US</h5>
    <div class="social">
      <div><i style="border-color:var(--orange)"></i>Faceboard</div><div><i style="border-color:var(--green)"></i>Chirper</div>
      <div><i style="border-color:var(--orange)"></i>Pinboard</div><div><i style="border-color:var(--orange)"></i>Globe+</div>
    </div>
    <div class="cards"><span></span><span></span><span></span><span></span><span></span></div></div>
</div>
<div class="abs bottom"><p>&copy;2016. PONDERMESHPATHS. ALL RIGHTS RESERVED.</p></div>
</body>
</html>
```